Bry7Legal Letterhead

Need a new letterhead for my law firm.
IDENTIFYING INFORMATION BELOW:
Anselmo R Quintara III
Attorney at Law
Address: 2847 Larkspur Blvd, Ste 300, Dallas, TX 75204
Phone: 877-482-6017
Fax: 469-738-1452
Email: bry@bry7legal.example
Website: www.bry7legal.example

Colors
0054AA
0677BA
7BADD7
CADEEF
E8F1F8

Requirements
Must have
• Logo needs to be on the letterhead, along with identifying information which is included in the project description.

```html
<!DOCTYPE html>
<html lang="en">
<head>
<meta charset="utf-8">
<title>Bry7Legal Letterhead</title>
<link href="https://fonts.googleapis.com/css2?family=Inter:wght@300;400;600;800&family=Arimo:wght@400&display=swap" rel="stylesheet">
<style>
  :root {
    --stage: #e4e6e9;
    --paper-light: #ffffff;
    --paper-shade: #d6d6d8;
    --ink: #111111;
    --body-ink: #4a4a4a;
    --accent: #0a97d6;
    --band-deep: #0054aa;
    --band-mid: #0677ba;
    --band-light: #11a6e0;
    --signature-tone: #c9ced6;
  }
  * { margin: 0; padding: 0; box-sizing: border-box; }
  html, body { width: 1039px; height: 1200px; overflow: hidden; background: var(--stage); }
  .letterhead {
    position: absolute; left: 117px; top: 33px; width: 805px; height: 1134px;
    background: linear-gradient(135deg, var(--paper-light) 0%, #ececed 45%, var(--paper-shade) 100%);
    font-family: "Inter", sans-serif; color: var(--ink);
  }
  .brand { position: absolute; left: 60px; top: 64px; width: 293px; text-align: center; }
  .brand-name { display: block; font-family: "Inter", sans-serif; font-weight: 800; font-size: 43px; line-height: 1; letter-spacing: 1px; color: var(--ink); }
  .brand-tagline { display: block; margin-top: 6px; font-weight: 300; font-size: 17px; letter-spacing: 2.6px; color: var(--ink); }
  .attorney { position: absolute; right: 70px; top: 76px; text-align: right; }
  .attorney-name { font-weight: 600; font-size: 19px; color: var(--accent); line-height: 1.1; }
  .attorney-title { margin-top: 4px; font-weight: 400; font-size: 12px; letter-spacing: 0.4px; }
  .letter { position: absolute; left: 60px; top: 372px; width: 681px; font-family: "Arimo", sans-serif; color: var(--body-ink); }
  .salutation { font-size: 16.5px; margin-bottom: 17px; }
  .letter p { font-size: 12.3px; line-height: 19px; text-align: justify; margin-bottom: 19px; hyphens: auto; }
  .closing { font-size: 12.3px; }
  .signature { position: absolute; left: 61px; top: 769px; width: 102px; height: 41px; background: linear-gradient(90deg, var(--signature-tone), rgba(201,206,214,0.3)); border-radius: 4px; }
  .contact { position: absolute; top: 1077px; font-size: 11.6px; line-height: 15px; color: var(--ink); }
  .contact-address { left: 63px; }
  .contact-phone { left: 355px; }
  .contact-web { left: 620px; }
  .contact-line { display: flex; align-items: center; gap: 5px; }
  .contact-line svg { width: 11px; height: 11px; fill: var(--accent); flex: none; }
  .footer-band { position: absolute; left: 0; bottom: 0; width: 100%; height: 9px;
    background: linear-gradient(90deg, var(--band-deep), var(--band-mid) 25%, var(--band-light) 50%, var(--band-mid) 75%, var(--band-deep)); }
</style>
</head>
<body>
<main class="letterhead">
  <header>
    <div class="brand">
      <span class="brand-name">Bry7Legal</span>
      <span class="brand-tagline">RIGHT BY YOUR SIDE</span>
    </div>
    <div class="attorney">
      <div class="attorney-name">ANSELMO R QUINTARA III</div>
      <div class="attorney-title">ATTORNEY AT LAW</div>
    </div>
  </header>

  <section class="letter">
    <div class="salutation">Dear Mr. Hallworth,</div>
    <p>Lorem ipsum dolor sit amet, consectetur adipiscing elit. Donec orci purus, luctus vitae dignissim eu, iaculis sed purus. Vivamus faucibus, ipsum nec aliquet viverra, leo mauris condimentum ligula, sit amet sagittis enim ligula quis arcu. Nam egestas tortor id nisi porttitor mattis. In tortor ante, ultricies in suscipit a, tempus non massa. Vivamus et auctor mi. Fusce vel massa nulla. Phasellus nec eros mauris, et scelerisque orci.</p>
    <p>Donec malesuada orci vitae nulla accumsan porta a id massa. Quisque accumsan iaculis magna sit amet fringilla. Maecenas consequat, magna eget tincidunt semper, odio nibh rutrum mi, id feugiat ante nisi eu risus. Vestibulum nunc orci, rhoncus a placerat in, ultricies in mi. Cras mattis varius eros, vel fringilla nisi suscipit eget. Quisque scelerisque sagittis nulla at porttitor.</p>
    <p>Sed id augue vitae urna euismod commodo aliquet a quam. Pellentesque arcu velit, cursus et malesuada ut, consequat et diam. Nullam erat sem, rhoncus id ullamcorper vitae, rhoncus et arcu. In ultricies ultricies nulla, ut rutrum nisi iaculis at. Donec eu magna a metus ornare faucibus. Fusce aliquet faucibus ultricies. Morbi semper, est id tincidunt gravida, sem arcu adipiscing lacus, ac bibendum nulla leo eu purus. Quisque nec diam sed risus consectetur a ccumsan quis quis nibh. Vestibulum id purus lorem.</p>
    <div class="closing">Sincerely,</div>
  </section>

  <div class="signature" role="img" aria-label="Handwritten signature of the attorney"></div>

  <footer>
    <address class="contact contact-address" style="font-style:normal">
      2847 Larkspur Blvd,<br>Ste 300, Dallas, TX 75204
    </address>
    <div class="contact contact-phone">
      <div class="contact-line">
        <svg viewBox="0 0 24 24" aria-hidden="true"><path d="M6.6 10.8a15.1 15.1 0 0 0 6.6 6.6l2.2-2.2c.3-.3.7-.4 1-.2 1.1.4 2.3.6 3.6.6.6 0 1 .4 1 1V20c0 .6-.4 1-1 1A17 17 0 0 1 3 4c0-.6.4-1 1-1h3.5c.6 0 1 .4 1 1 0 1.3.2 2.5.6 3.6.1.3 0 .7-.2 1z"/></svg>
        <span>877-482-6017</span>
      </div>
      <div class="contact-line">
        <svg viewBox="0 0 24 24" aria-hidden="true"><path d="M6 2h12v5H6zM3 8h18a2 2 0 0 1 2 2v7h-4v5H5v-5H1v-7a2 2 0 0 1 2-2zm4 8v4h10v-4z"/></svg>
        <span>469-738-1452</span>
      </div>
    </div>
    <div class="contact contact-web">
      <div class="contact-line">
        <svg viewBox="0 0 24 24" aria-hidden="true"><path d="M2 5h20v14H2zm2 2v.5l8 5 8-5V7l-8 5z"/></svg>
        <span>bry@bry7legal.example</span>
      </div>
      <div class="contact-line">
        <svg viewBox="0 0 24 24" aria-hidden="true"><path d="M12 2a10 10 0 1 0 0 20 10 10 0 0 0 0-20zm0 2c.9 1.2 1.7 2.8 2 5h-4c.3-2.2 1.1-3.8 2-5zM9.8 4.4A11 11 0 0 0 8 9H4.6a8 8 0 0 1 5.2-4.6zm4.4 0A8 8 0 0 1 19.4 9H16a11 11 0 0 0-1.8-4.6zM4.1 11H8v2H4.1a8 8 0 0 1 0-2zM10 11h4v2h-4zm6 0h3.9a8 8 0 0 1 0 2H16zM4.6 15H8a11 11 0 0 0 1.8 4.6A8 8 0 0 1 4.6 15zM10 15h4c-.3 2.2-1.1 3.8-2 5-.9-1.2-1.7-2.8-2-5zm6 0h3.4a8 8 0 0 1-5.2 4.6A11 11 0 0 0 16 15z"/></svg>
        <span>www.bry7legal.example</span>
      </div>
    </div>
    <div class="footer-band"></div>
  </footer>
</main>
</body>
</html>
```